business card deign

Logo needs the following on it.
1. attached logo
2. Tagline - "From icy coolers to loud speakers...we bring the fun!"
3. Name- Dalton Pikes, Founder and CPO
4. Address - 412 E. Carver Avenue, Ste 2207, Marlow Bay, FL. 33917
5. Phone - 555.318.4726

```html
<!DOCTYPE html>
<html lang="en">
<head>
<meta charset="utf-8">
<title>Bounder business card</title>
<link rel="stylesheet" href="https://fonts.googleapis.com/css2?family=Roboto:wght@400;500;700&display=swap">
<style>
  :root {
    --backdrop: #222222;
    --card: #161616;
    --ink: #ffffff;
    --ink-soft: #e6e6e6;
    --pattern-dark: #121212;
    --pattern-mid: #2a2a2a;
    --pattern-light: #8a8a8a;
    --mark-faint: rgba(255,255,255,.06);
  }
  * { box-sizing: border-box; margin: 0; padding: 0; }
  html, body {
    width: 1200px; height: 780px; overflow: hidden;
    background: var(--backdrop);
    font-family: "Roboto", Arial, sans-serif;
    color: var(--ink);
  }
  .stage { position: relative; width: 1200px; height: 780px; }

  .card {
    position: absolute; top: 235px; width: 540px; height: 310px;
    background: var(--card); border-radius: 22px; overflow: hidden;
    box-shadow: 0 14px 30px rgba(0,0,0,.55);
  }
  .card--back { left: 40px; }
  .card--front { left: 620px; }

  .back-pattern {
    position: absolute; inset: 0;
    background: linear-gradient(135deg, var(--pattern-light) 0%, var(--pattern-mid) 35%, var(--pattern-dark) 100%);
    opacity: .55;
  }

  .faint-mark {
    position: absolute; left: 150px; top: 110px; width: 160px; height: 200px;
    background: radial-gradient(ellipse at center, var(--mark-faint), rgba(255,255,255,0) 70%);
  }

  .brand {
    position: absolute; right: 34px; top: 62px;
    display: flex; align-items: center; gap: 14px;
  }
  .brand-dot { width: 16px; height: 16px; border-radius: 50%; background: var(--ink); }
  .brand-name {
    font-weight: 700; font-size: 28px; letter-spacing: 12px; margin-right: -12px;
    color: var(--ink);
  }

  .person-bar {
    position: absolute; left: 0; top: 148px; width: 12px; height: 58px; background: var(--ink);
  }
  .person { position: absolute; left: 34px; top: 146px; }
  .person-name { font-weight: 700; font-size: 26px; line-height: 1.1; }
  .person-role { font-weight: 400; font-size: 16px; line-height: 1.2; margin-top: 4px; color: var(--ink-soft); }

  .divider {
    position: absolute; left: 34px; right: 28px; top: 214px;
    height: 1.5px; background: var(--ink);
  }

  .contact {
    position: absolute; right: 28px; top: 226px;
    font-style: normal; text-align: right;
    font-size: 13px; line-height: 1.55; color: var(--ink-soft);
  }
  .contact-line { display: flex; justify-content: flex-end; align-items: center; gap: 8px; }
  .contact-line svg { width: 14px; height: 14px; flex: none; }
  .contact-line--plain { padding-right: 22px; }

  .tagline {
    position: absolute; left: 34px; top: 240px; width: 220px;
    font-size: 14px; line-height: 1.35; color: var(--ink-soft);
  }
</style>
</head>
<body>
<main class="stage">
  <section class="card card--back">
    <div class="back-pattern" role="img" aria-label="Repeating brand emblem pattern fading from silver at the top left to black"></div>
  </section>

  <section class="card card--front">
    <div class="faint-mark" role="img" aria-label="Large faint brand emblem in the background"></div>

    <div class="brand">
      <span class="brand-dot"></span>
      <span class="brand-name">BOUNDER</span>
    </div>

    <div class="person-bar"></div>
    <div class="person">
      <p class="person-name">Dalton Pikes</p>
      <p class="person-role">Founder and CPO</p>
    </div>

    <div class="divider"></div>

    <address class="contact">
      <div class="contact-line">
        <span>555.318.4726</span>
        <svg viewBox="0 0 24 24" aria-hidden="true"><path fill="none" stroke="#fff" stroke-width="2" d="M5 3h4l2 5-3 2a11 11 0 0 0 6 6l2-3 5 2v4a2 2 0 0 1-2 2A17 17 0 0 1 3 5a2 2 0 0 1 2-2z"/></svg>
      </div>
      <div class="contact-line">
        <span>412 E. Carver Avenue,</span>
        <svg viewBox="0 0 24 24" aria-hidden="true"><path fill="none" stroke="#fff" stroke-width="2" d="M12 22s7-7 7-12a7 7 0 0 0-14 0c0 5 7 12 7 12z"/><circle cx="12" cy="10" r="2.5" fill="none" stroke="#fff" stroke-width="2"/></svg>
      </div>
      <div class="contact-line contact-line--plain">
        <span>Ste 2207, Marlow Bay, FL. 33917</span>
      </div>
    </address>

    <p class="tagline">From icy coolers to loud speakers...we bring the fun!</p>
  </section>
</main>
</body>
</html>
```